Harbourline Physiotherapy business card design

We need a fresh, new business card design for our physiotherapy clinic Harbourline Physiotherapy

Will attach logo soon we had logo designed from our last project

Industry/Entity Type

Physical Therapy

Contact Information for Business Card

On front
Needs our logo, contact details:
58 Wexley Lane Marrowby NSW 2861
Ph/f: 02 9481 2057
info@harbourlinephysio.example.com.au

Requirements
Must have
• On the back of the card needs to have area to write down follow up appointments
• On front
• Needs our logo
• The colours have to be the colours in our logo which are: sky blue, black and white
• Font to be same as our logo please
• We want the card to look simple, not too cluttered but to the point
Should not have
• We don't need any extra pictures other than our logo

```html
<!DOCTYPE html>
<html lang="en">
<head>
<meta charset="utf-8">
<title>Harbourline Physiotherapy – Business Card</title>
<link href="https://fonts.googleapis.com/css2?family=Open+Sans:wght@400;600;700&display=swap" rel="stylesheet">
<style>
  :root {
    --stage: #2b2b2d;
    --card-white: #ffffff;
    --card-black: #050505;
    --sky: #2f7fd0;
    --sky-light: #4a9be6;
    --rule-white: #f2f2f2;
  }
  * { box-sizing: border-box; margin: 0; padding: 0; }
  html, body {
    width: 1200px; height: 900px; overflow: hidden;
    background: var(--stage);
    font-family: "Open Sans", Arial, sans-serif;
  }
  .canvas { position: relative; width: 1200px; height: 900px; }

  .card {
    position: absolute;
    width: 660px; height: 390px;
    border-radius: 26px;
    overflow: hidden;
    box-shadow: 0 18px 40px rgba(0,0,0,0.45);
  }

  .brand { position: absolute; display: flex; align-items: center; gap: 12px; }
  .brand__dot { width: 34px; height: 34px; border-radius: 50%; background: var(--sky); flex: none; }
  .brand__name { font-weight: 700; color: var(--sky); line-height: 1.05; font-size: 30px; }

  /* Appointment side */
  .card--appointment { left: 150px; top: 40px; background: var(--card-white); }
  .card--appointment .brand { left: 250px; top: 70px; }

  .appointments { position: absolute; left: 48px; top: 218px; color: var(--sky); font-size: 17px; }
  .appointments__title { margin-bottom: 8px; }
  .appointments__row { display: flex; align-items: flex-end; height: 36px; }
  .appointments__label { width: 62px; }
  .appointments__line { width: 300px; border-bottom: 1.5px dashed var(--sky-light); margin-bottom: 5px; }

  /* Contact side */
  .card--contact { left: 390px; top: 470px; background: var(--card-black); }
  .card--contact .brand { left: 44px; top: 52px; }

  .address {
    position: absolute; right: 36px; top: 168px;
    color: var(--sky); font-size: 15px; text-align: right; line-height: 1.35;
  }
  .holder {
    position: absolute; left: 44px; top: 188px;
    font-size: 30px; font-weight: 700; color: var(--sky); letter-spacing: 0.5px; line-height: 1.3;
  }
  .divider { position: absolute; left: 44px; top: 228px; right: 0; height: 3px; }
  .divider__white { position: absolute; left: 0; top: 0; width: 228px; height: 3px; background: var(--rule-white); }
  .divider__blue { position: absolute; left: 228px; top: 1px; right: 0; height: 1.5px; background: var(--sky); }
  .contact-list { position: absolute; left: 44px; top: 254px; list-style: none; color: var(--sky); font-size: 16px; }
  .contact-list li { display: flex; align-items: center; gap: 12px; height: 28px; }
  .contact-list svg { width: 15px; height: 15px; flex: none; }
</style>
</head>
<body>
<main class="canvas">

  <section class="card card--appointment" aria-label="Appointment side">
    <div class="brand">
      <span class="brand__dot"></span>
      <span class="brand__name">Harbourline<br>Physiotherapy</span>
    </div>
    <div class="appointments">
      <p class="appointments__title">Appointments:</p>
      <div class="appointments__row"><span class="appointments__label">Name:</span><span class="appointments__line"></span></div>
      <div class="appointments__row"><span class="appointments__label">Time:</span><span class="appointments__line"></span></div>
      <div class="appointments__row"><span class="appointments__label">Date:</span><span class="appointments__line"></span></div>
    </div>
  </section>

  <section class="card card--contact" aria-label="Contact side">
    <div class="brand">
      <span class="brand__dot"></span>
      <span class="brand__name">Harbourline<br>Physiotherapy</span>
    </div>
    <p class="address">58 Wexley Lane<br>Marrowby NSW 2861</p>
    <p class="holder">MARA ELLIS</p>
    <div class="divider"><span class="divider__white"></span><span class="divider__blue"></span></div>
    <ul class="contact-list">
      <li>
        <svg viewBox="0 0 16 16" aria-hidden="true"><path fill="#ffffff" d="M3.2 1.2l2.3 0 1 3.4-1.6 1.2c.8 1.9 2.3 3.4 4.2 4.2l1.2-1.6 3.4 1v2.3c0 .8-.7 1.5-1.5 1.5C6.5 13.2 2.8 9.5 1.7 2.7c0-.8.7-1.5 1.5-1.5z"/></svg>
        <span>02 9481 2057</span>
      </li>
      <li>
        <svg viewBox="0 0 16 16" aria-hidden="true"><rect x="1.5" y="3.5" width="13" height="9" rx="1" fill="none" stroke="#ffffff" stroke-width="1.4"/><path d="M1.8 4l6.2 4.8L14.2 4" fill="none" stroke="#ffffff" stroke-width="1.4"/></svg>
        <span>info@harbourlinephysio.example.com.au</span>
      </li>
    </ul>
  </section>

</main>
</body>
</html>
```